UI Redesign For Mobile Events iPhone App

We need a new UI design for our Social Events mobile app. Our app called Vessa is geared to help users find trending events in their local area. We show visual metrics on percent full and male female ratio and age group ratings. We want people to see whats going on at event before they get there through our app. Also we have a group chat portion to our app that we need included in the design. We would like to see a fresh, clean, and easy to use user interface that uses colors like, purple, blue and or hot pink.You may visit our website myvessa.example for more information about what our app is geared to do.
Updates

Target Market(s)

Our target market people that use social networks and attend social events ranging from ages 16-44.

Industry/Entity Type

Events

Requirements
Must have
• We would like to see an Example layout of all screens. (UPDATE: Please use our current background in your design, A PSD has been uploaded for you to grab the background. The Vessa Logo is NOT required to be included at the top of every screen)

-Profile Screen: Shows points earned, events attending, events created
-Event Listings Screen: Must have large image for event, visual metrics, date& time, location, attend button, invite friends button, Label for user who created the event
-Event Description Page: Shows everything as the event listing, has a description of the event, shows friends that are attending, points available
-Group Messaging Screen
-Slide Out Navigation Screen
-Notification Screen
-Ticket Screen
-Friends Activity Screen
-Friends Profile View: Shows events they've attended and points they've earned under their contact picture; invite button
-Sign-In Screen
-Register Screen

A way to label/categorize our different types of events:
-Nightlife
-Family
-Live Music & Concerts
-Restaurants
Group Chat Layout
Visual Meters for Percent Full, Male Female Ratio, Age Rating

```html
<!DOCTYPE html>
<html lang="en">
<head>
<meta charset="utf-8">
<title>Vessa — App Screens</title>
<link href="https://fonts.googleapis.com/css2?family=Roboto:wght@300;400;500;700&display=swap" rel="stylesheet">
<style>
:root{
  --page:#ece4e6;
  --ink:#ffffff;
  --night:#0b0b16;
  --menu:#1d1222;
  --purple:#4b1a8f;
  --purple-hi:#5b2b99;
  --pink:#ee1653;
  --blue:#0a62f0;
  --sky:#1a9ef0;
  --navy:#1a3a8e;
  --violet-text:#4d1c9a;
  --panel:rgba(215,225,235,.55);
  --row:rgba(200,210,225,.45);
  --line:rgba(255,255,255,.45);
  --dark-dot:#222226;
  --green:#2ecc40;
  --gold:#f5b800;
}
*{box-sizing:border-box;margin:0;padding:0}
html,body{width:1200px;height:1000px;overflow:hidden}
body{background:radial-gradient(ellipse at 50% 45%,#faf7f8 0%,var(--page) 75%,#e3d8db 100%);font-family:"Roboto",Arial,sans-serif;color:var(--ink);position:relative}
.screen{position:absolute;width:256px;height:454px;overflow:hidden;background:var(--night)}
.backdrop{position:absolute;inset:0;background:
  radial-gradient(circle at 22% 18%,rgba(255,120,200,.75) 0,rgba(255,120,200,0) 28%),
  radial-gradient(circle at 60% 22%,rgba(80,200,255,.8) 0,rgba(80,200,255,0) 42%),
  radial-gradient(circle at 85% 55%,rgba(230,90,200,.55) 0,rgba(230,90,200,0) 30%),
  radial-gradient(circle at 30% 60%,rgba(60,120,220,.55) 0,rgba(60,120,220,0) 40%),
  linear-gradient(180deg,#1b3f78 0%,#244a86 40%,#0d0d1d 80%,#050509 100%)}
.status{position:absolute;top:0;left:0;right:0;height:16px;font-size:8.5px;font-weight:500;display:flex;align-items:center;justify-content:space-between;padding:0 5px;z-index:3}
.status .time{position:absolute;left:0;right:0;text-align:center}
.status .batt{display:flex;align-items:center;gap:3px}
.status .batt i{display:inline-block;width:16px;height:7px;border:1px solid #fff;background:#fff;border-radius:1px}
.header{position:absolute;top:20px;left:0;right:0;height:40px;display:flex;align-items:center;justify-content:center;z-index:2}
.header h1{font-weight:300;font-size:26px;letter-spacing:.2px}
.header .left,.header .right{position:absolute;top:8px;width:24px;height:24px}
.header .left{left:8px}.header .right{right:8px}
.btn{position:absolute;display:flex;align-items:center;justify-content:center;font-size:14px;font-weight:300;color:#fff;gap:10px}
.btn.pink{background:var(--pink)}.btn.purple{background:var(--purple)}.btn.blue{background:var(--blue)}
.btn.navy{background:var(--navy)}.btn.sky{background:var(--sky)}
.wide{left:8px;width:240px;height:35px}
.half-l{left:8px;width:116px;height:35px}.half-r{left:132px;width:116px;height:35px}

/* login */
.brand{position:absolute;top:70px;left:55px;display:flex;align-items:center;gap:14px}
.brand .mark{width:40px;height:40px;border-radius:50%;background:#6b4aa8}
.brand span{font-size:26px;font-weight:300;letter-spacing:2px}
.field{position:absolute;left:8px;width:240px;height:34px;background:rgba(230,235,245,.5);color:#1b1b2a;font-size:12px;display:flex;align-items:center;padding-left:15px}
.field+.field{border-top:1px solid rgba(255,255,255,.6)}

/* menu */
.menu{position:absolute;left:0;top:16px;bottom:0;width:145px;background:var(--menu);z-index:2}
.menu li{list-style:none;height:45px;display:flex;align-items:center;gap:12px;padding-left:14px;font-size:12px;font-weight:300;border-bottom:1px solid rgba(255,255,255,.08)}
.menu li.active{background:var(--purple-hi)}
.menu svg{width:18px;height:18px}

/* friends */
.selector{position:absolute;left:8px;width:240px;top:76px;height:35px;background:var(--blue);font-size:14px;font-weight:300;display:flex;align-items:center;justify-content:center}
.selector .chev{position:absolute;right:12px;width:14px;height:14px;border-radius:50%;background:#fff}
.friends{position:absolute;left:8px;width:240px;top:123px;height:272px;background:var(--panel)}
.friends .bar{height:37px;border-bottom:1px solid var(--line);display:flex;align-items:center;padding:0 10px;font-size:11px;color:#222;gap:14px}
.friends .add{margin-left:auto;color:var(--blue);font-size:12px;display:flex;align-items:center;gap:5px}
.friend{position:absolute;width:50px;text-align:center;font-size:9px;color:#555}
.friend i{display:block;width:48px;height:48px;margin:0 auto 2px;border-radius:50%;background:var(--dark-dot);border:2px solid #fff}
.scroll{position:absolute;right:6px;top:48px;width:2px;height:210px;background:rgba(255,255,255,.4)}
.scroll b{display:block;height:80px;background:var(--purple)}

/* messages */
.tabs{position:absolute;left:8px;width:240px;top:70px;height:35px;background:rgba(235,240,245,.85);display:flex}
.tabs div{flex:1;display:flex;align-items:center;justify-content:center;border-right:1px solid #ccc}
.online{position:absolute;left:8px;top:59px;background:var(--green);font-size:6px;font-weight:700;padding:2px 10px 2px 6px;clip-path:polygon(0 0,100% 0,88% 100%,0 100%)}
.thread{position:absolute;left:8px;width:240px;top:105px;height:288px;background:var(--panel);overflow:hidden}
.msg{height:48px;display:flex;align-items:center;padding:0 8px 0 6px;gap:8px;border-bottom:1px solid var(--line);color:#111;position:relative}
.msg i{width:40px;height:40px;border-radius:50%;background:var(--dark-dot);flex:none}
.msg b{display:block;font-weight:400;font-size:9.5px}
.msg span{font-size:7.5px}
.msg em{position:absolute;right:18px;top:10px;font-style:normal;font-size:7px;color:#fff}

/* events */
.featured{position:absolute;left:8px;top:57px;background:var(--gold);font-size:5.5px;font-weight:700;padding:2px 14px 2px 5px;clip-path:polygon(0 0,100% 0,88% 100%,0 100%);z-index:2}
.card{position:absolute;left:8px;width:240px;background:#fff;color:#111}
.card .head{height:37px;padding:3px 4px;position:relative;border-bottom:1px solid #ddd}
.card .head h2{font-size:10.5px;font-weight:400;color:var(--violet-text);line-height:12px}
.card .head p{font-size:7.5px;font-weight:700;line-height:9px}
.card .head small{display:block;font-size:5.5px;line-height:7px}
.card .price{position:absolute;right:0;top:0;bottom:0;width:34px;border-left:1px solid #ddd;display:flex;align-items:center;justify-content:center;font-size:8.5px;color:var(--pink)}
.photo{height:100px}
.photo.fest{background:linear-gradient(180deg,#f4f4f2 0%,#c9d4d0 25%,#d8a030 45%,#d8343a 70%,#7c7c7c 100%)}
.photo.plaza{background:linear-gradient(180deg,#e8eef2 0%,#c9d6e0 30%,#3c6ea8 55%,#6f8f3c 75%,#6d6d6d 100%)}
.card .foot{height:27px;display:flex;align-items:center;padding:0 4px;gap:6px;font-size:5.5px;color:var(--violet-text);position:relative}
.card .foot .who{color:#666;font-size:5px;width:58px;line-height:6px}
.card .foot .ratio{margin-left:auto;font-size:7.5px;color:var(--violet-text);display:flex;align-items:center;gap:4px}
.dot{display:inline-block;width:7px;height:7px;background:var(--violet-text);border-radius:2px}

/* details */
.titlebar{position:absolute;left:8px;width:240px;top:68px;height:37px;background:#fff;color:var(--violet-text);font-size:12px;display:flex;align-items:center;justify-content:center}
.info{position:absolute;left:8px;width:240px;height:25px;background:var(--row);border-bottom:1px solid var(--line);display:flex;align-items:center;gap:10px;padding-left:10px;font-size:7.5px;color:#fff}
.meters{position:absolute;left:8px;width:240px;top:332px;height:60px;background:var(--row);display:flex}
.meters div{flex:1;display:flex;flex-direction:column;align-items:center;justify-content:center;font-size:7px;gap:2px}
.meters div+div{border-left:1px solid var(--line)}

/* forms */
.form{position:absolute;left:8px;width:240px;top:70px;background:var(--panel)}
.form .r{height:35px;display:flex;border-bottom:1px solid var(--line);font-size:8.5px;color:#111}
.form .r label{width:50px;background:rgba(235,240,245,.55);display:flex;align-items:center;justify-content:flex-end;padding-right:6px;border-right:1px solid var(--line)}
.form .r span{display:flex;align-items:center;padding-left:4px}
.terms{position:absolute;left:0;right:0;top:368px;text-align:center;font-size:13px;font-weight:300;text-decoration:underline}
</style>
</head>
<body>

<!-- ============ Row 1 ============ -->

<!-- Sign in -->
<section class="screen" style="left:31px;top:33px">
  <div class="backdrop" role="img" aria-label="Blurred concert crowd with stage lights in blue and pink"></div>
  <div class="status"><span>●●●○○ CELL</span><span class="time">4:21 PM</span><span class="batt">100% <i></i></span></div>
  <div class="brand"><div class="mark"></div><span>VESSA</span></div>
  <div class="field" style="top:170px">username</div>
  <div class="field" style="top:204px">password</div>
  <div class="btn pink half-l" style="top:250px">Sign Up</div>
  <div class="btn purple half-r" style="top:250px">Sign In</div>
  <div class="btn navy wide" style="top:327px">Log In with Linkly</div>
  <div class="btn sky wide" style="top:371px">Log In with Chirpr</div>
</section>

<!-- Slide-out navigation -->
<section class="screen" style="left:324px;top:33px">
  <div class="backdrop" role="img" aria-label="Blurred concert crowd with stage lights in blue and pink"></div>
  <div class="status" style="background:var(--menu)"><span>●●●○○ CELL</span><span class="time">4:21 PM</span><span class="batt">100% <i></i></span></div>
  <ul class="menu">
    <li><svg viewBox="0 0 20 20" fill="none" stroke="#fff"><circle cx="8" cy="6" r="3.5"/><circle cx="13" cy="13" r="3.5"/></svg>Profile</li>
    <li><svg viewBox="0 0 20 20" fill="none" stroke="#fff"><rect x="2" y="5" width="16" height="11"/><path d="M2 5l8 6 8-6"/></svg>Messages</li>
    <li><svg viewBox="0 0 20 20" fill="none" stroke="#fff"><path d="M5 14V9a5 5 0 0110 0v5l2 2H3z"/><path d="M8 17h4"/></svg>Notifications</li>
    <li class="active"><svg viewBox="0 0 20 20" fill="none" stroke="#fff"><circle cx="10" cy="10" r="6.5"/></svg>My Vessa</li>
    <li><svg viewBox="0 0 20 20" fill="none" stroke="#fff"><path d="M3 10l7-7h7v7l-7 7z"/><circle cx="13.5" cy="6.5" r="1"/></svg>Tickets</li>
    <li><svg viewBox="0 0 20 20" fill="none" stroke="#fff"><circle cx="10" cy="10" r="3"/><circle cx="10" cy="10" r="7" stroke-dasharray="2 2"/></svg>Events</li>
  </ul>
  <div class="header" style="justify-content:flex-start;left:145px">
    <svg style="position:absolute;left:8px;top:10px" width="22" height="18" viewBox="0 0 22 18" stroke="#fff" stroke-width="2"><path d="M0 2h22M0 9h22M0 16h22"/></svg>
    <h1 style="position:absolute;left:72px">Edit</h1>
  </div>
  <div class="selector" style="left:153px"></div>
  <div class="friends" style="left:153px">
    <div class="bar">FRIENDS <svg width="14" height="14" viewBox="0 0 14 14" fill="var(--purple)"><circle cx="2" cy="2" r="1.8"/><circle cx="7" cy="2" r="1.8"/><circle cx="12" cy="2" r="1.8"/><circle cx="2" cy="7" r="1.8"/><circle cx="7" cy="7" r="1.8"/><circle cx="12" cy="7" r="1.8"/><circle cx="2" cy="12" r="1.8"/><circle cx="7" cy="12" r="1.8"/><circle cx="12" cy="12" r="1.8"/></svg></div>
    <div class="friend" style="left:9px;top:48px"><i></i>user1</div>
    <div class="friend" style="left:82px;top:48px"><i></i>user2</div>
    <div class="friend" style="left:9px;top:120px"><i></i>user4</div>
    <div class="friend" style="left:82px;top:120px"><i></i>user5</div>
    <div class="friend" style="left:9px;top:192px"><i></i>user7</div>
    <div class="friend" style="left:82px;top:192px"><i></i>user8</div>
  </div>
  <div class="btn pink" style="left:153px;width:110px;top:410px;height:35px"></div>
</section>

<!-- Edit group -->
<section class="screen" style="left:616px;top:33px">
  <div class="backdrop" role="img" aria-label="Blurred concert crowd with stage lights in blue and pink"></div>
  <div class="status"><span>●●●○○ CELL</span><span class="time">4:21 PM</span><span class="batt">100% <i></i></span></div>
  <div class="header">
    <svg class="left" viewBox="0 0 24 24" stroke="#fff" stroke-width="2"><path d="M1 5h22M1 12h22M1 19h22"/></svg>
    <h1>Edit Vessa</h1>
  </div>
  <div class="selector">Sloths <span class="chev"><svg width="14" height="14" viewBox="0 0 14 14" fill="none" stroke="var(--blue)" stroke-width="2"><path d="M4 6l3 3 3-3"/></svg></span></div>
  <div class="friends">
    <div class="bar">FRIENDS
      <svg width="14" height="14" viewBox="0 0 14 14" fill="var(--purple)"><circle cx="2" cy="2" r="1.8"/><circle cx="7" cy="2" r="1.8"/><circle cx="12" cy="2" r="1.8"/><circle cx="2" cy="7" r="1.8"/><circle cx="7" cy="7" r="1.8"/><circle cx="12" cy="7" r="1.8"/><circle cx="2" cy="12" r="1.8"/><circle cx="7" cy="12" r="1.8"/><circle cx="12" cy="12" r="1.8"/></svg>
      <svg width="16" height="14" viewBox="0 0 16 14" stroke="#222" stroke-width="1.5"><path d="M0 1h16M0 5h16M0 9h16M0 13h16"/></svg>
      <span class="add"><svg width="14" height="14" viewBox="0 0 14 14"><circle cx="7" cy="7" r="7" fill="var(--blue)"/><path d="M7 3v8M3 7h8" stroke="#fff" stroke-width="1.5"/></svg>Add</span>
    </div>
    <div class="friend" style="left:14px;top:48px"><i></i>user1</div>
    <div class="friend" style="left:86px;top:48px"><i></i>user1</div>
    <div class="friend" style="left:158px;top:48px"><i></i>user3</div>
    <div class="friend" style="left:14px;top:120px"><i></i>user4</div>
    <div class="friend" style="left:86px;top:120px"><i></i>user5</div>
    <div class="friend" style="left:158px;top:120px"><i></i>user6</div>
    <div class="friend" style="left:14px;top:192px"><i></i>user7</div>
    <div class="friend" style="left:86px;top:192px"><i></i>user8</div>
    <div class="friend" style="left:158px;top:192px"><i></i>user9</div>
    <div class="scroll"><b></b></div>
  </div>
  <div class="btn purple wide" style="top:410px">Save</div>
</section>

<!-- Messages -->
<section class="screen" style="left:909px;top:33px">
  <div class="backdrop" role="img" aria-label="Blurred concert crowd with stage lights in blue and pink"></div>
  <div class="status"><span>●●●○○ CELL</span><span class="time">4:21 PM</span><span class="batt">100% <i></i></span></div>
  <div class="header">
    <svg class="left" viewBox="0 0 24 24" fill="none" stroke="#fff" stroke-width="2"><path d="M22 12H3M11 4l-8 8 8 8"/></svg>
    <h1>Messages</h1>
    <svg class="right" viewBox="0 0 24 24" stroke="#fff" stroke-width="2"><path d="M12 1v22M1 12h22"/></svg>
  </div>
  <div class="tabs">
    <div><svg width="16" height="16" viewBox="0 0 16 16"><circle cx="8" cy="8" r="8" fill="#999"/><path d="M8 3v5h3" stroke="#fff" fill="none"/></svg></div>
    <div><svg width="18" height="18" viewBox="0 0 18 18"><circle cx="9" cy="9" r="9" fill="var(--purple)"/><circle cx="9" cy="7" r="3" fill="#fff"/><path d="M3.5 15a6 6 0 0111 0" fill="#fff"/></svg></div>
    <div style="border:0;color:#888;font-size:14px;letter-spacing:2px">•••</div>
  </div>
  <div class="online">ONLINE</div>
  <div class="thread">
    <div class="msg"><i></i><div><b>User1</b><span>Hey there! XD</span></div><em>5m</em></div>
    <div class="msg"><i></i><div><b>User 2</b><span>Good day. How are you?</span></div><em>10h</em></div>
    <div class="msg"><i></i><div><b>User 3</b><span>Will you attend? ;)</span></div><em>1d</em></div>
    <div class="msg"><i></i><div><b>User 4</b><span>I don't think so. I'll try. :(</span></div><em>2d</em></div>
    <div class="msg"><i></i><div><b>User 5</b><span>Just call me if you'll make it.</span></div><em>3d</em></div>
    <div class="msg"><i></i><div><b>User 6</b><span>:) No, no, no.....</span></div><em>3d</em></div>
    <div class="scroll" style="right:8px;top:6px;height:270px"><b style="margin-top:58px;height:86px"></b></div>
  </div>
  <div class="btn pink wide" style="top:410px">
    <svg width="16" height="18" viewBox="0 0 16 18" fill="none" stroke="#fff"><path d="M1 4h14M5 4V2h6v2M3 4l1 13h8l1-13M6 7v8M10 7v8"/></svg>Delete All</div>
</section>

<!-- ============ Row 2 ============ -->

<!-- Events -->
<section class="screen" style="left:31px;top:518px">
  <div class="backdrop" role="img" aria-label="Blurred concert crowd with stage lights in blue and pink"></div>
  <div class="status"><span>●●●○○ CELL</span><span class="time">4:21 PM</span><span class="batt">100% <i></i></span></div>
  <div class="header">
    <svg class="left" viewBox="0 0 24 24" stroke="#fff" stroke-width="2"><path d="M1 5h22M1 12h22M1 19h22"/></svg>
    <h1>Events</h1>
    <svg class="right" viewBox="0 0 24 24" stroke="#fff" stroke-width="2"><path d="M12 1v22M1 12h22"/></svg>
  </div>
  <div class="featured">★ FEATURED</div>
  <article class="card" style="top:68px">
    <div class="head"><h2>SUNWAVE FESTIVAL 2014</h2><p>Coral City, Philippines</p><small>Friday, 10Jan @ 8:0 AM</small><div class="price">Free</div></div>
    <div class="photo fest" role="img" aria-label="Street parade with dancers in bright festival costumes"></div>
    <div class="foot"><span><span class="dot"></span> Unjoin</span><span><span class="dot"></span> Invite Others</span><span class="who">You, Mia &amp; Jo are joining</span>
      <svg width="20" height="20" viewBox="0 0 20 20"><circle cx="10" cy="10" r="8" fill="none" stroke="#ddd" stroke-width="2"/><circle cx="10" cy="10" r="8" fill="none" stroke="var(--gold)" stroke-width="2" stroke-dasharray="37.7 50.3" transform="rotate(-90 10 10)"/><text x="10" y="12" font-size="5" text-anchor="middle" fill="#333">75%</text></svg>
      <span class="ratio">M/F Ratio <svg width="20" height="20" viewBox="0 0 20 20"><circle cx="10" cy="10" r="8" fill="none" stroke="var(--pink)" stroke-width="2"/><path d="M10 2a8 8 0 000 16" fill="none" stroke="var(--blue)" stroke-width="2"/></svg></span></div>
  </article>
  <article class="card" style="top:247px">
    <div class="head"><h2>METRO PLAZA SUMMER WORKSHOP</h2><p>Riverbend City, Philippines</p><small>Tuesday, 01April @ 8:0 AM</small><div class="price">$20</div></div>
    <div class="photo plaza" role="img" aria-label="Shopping mall building beside a tree-lined road"></div>
    <div class="foot"><span><span class="dot"></span> Join</span><span><span class="dot"></span> Invite Others</span><span class="who">Ana is joining</span>
      <svg width="20" height="20" viewBox="0 0 20 20"><circle cx="10" cy="10" r="8" fill="none" stroke="#ddd" stroke-width="2"/><circle cx="10" cy="10" r="8" fill="none" stroke="var(--gold)" stroke-width="2" stroke-dasharray="37.7 50.3" transform="rotate(-90 10 10)"/><text x="10" y="12" font-size="5" text-anchor="middle" fill="#333">75%</text></svg>
      <span class="ratio">M/F Ratio <svg width="20" height="20" viewBox="0 0 20 20"><circle cx="10" cy="10" r="8" fill="none" stroke="var(--pink)" stroke-width="2"/><path d="M10 2a8 8 0 000 16" fill="none" stroke="var(--blue)" stroke-width="2"/></svg></span></div>
  </article>
  <article class="card" style="top:425px">
    <div class="head"><h2>SUMMER PHOTOGRAPHY CONTEST</h2><p>Highfield, Northvale, Philippines</p><div class="price">$25</div></div>
  </article>
</section>

<!-- Details -->
<section class="screen" style="left:324px;top:518px">
  <div class="backdrop" role="img" aria-label="Blurred concert crowd with stage lights in blue and pink"></div>
  <div class="status"><span>●●●○○ CELL</span><span class="time">4:21 PM</span><span class="batt">100% <i></i></span></div>
  <div class="header">
    <svg class="left" viewBox="0 0 24 24" fill="none" stroke="#fff" stroke-width="2"><path d="M22 12H3M11 4l-8 8 8 8"/></svg>
    <h1>Details</h1>
    <svg class="right" viewBox="0 0 24 24" stroke="#fff" stroke-width="2"><path d="M12 1v22M1 12h22"/></svg>
  </div>
  <div class="featured">★ FEATURED</div>
  <div class="titlebar">SUNWAVE FESTIVAL 2014</div>
  <div class="card" style="top:105px">
    <div class="photo fest" role="img" aria-label="Street parade with dancers in bright festival costumes"></div>
    <div class="foot" style="height:25px"><span><span class="dot"></span> Unjoin</span><span><span class="dot"></span> Invite Others</span><span class="who" style="width:auto">You, Mia &amp; Jo are joining</span></div>
  </div>
  <div class="info" style="top:230px"><svg width="10" height="12" viewBox="0 0 10 12" fill="#fff"><path d="M5 0a4 4 0 014 4c0 3-4 8-4 8S1 7 1 4a4 4 0 014-4z"/><circle cx="5" cy="4" r="1.5" fill="#7c8aa0"/></svg>Coral City, Philippines</div>
  <div class="info" style="top:255px"><svg width="10" height="10" viewBox="0 0 10 10" fill="none" stroke="#fff"><rect x=".5" y="1.5" width="9" height="8"/><path d="M.5 4h9"/></svg>Friday, 10Jan @ 8:0 AM</div>
  <div class="info" style="top:280px"><svg width="10" height="10" viewBox="0 0 10 10" fill="#fff"><path d="M0 5l5-5h5v5l-5 5z"/></svg>FREE</div>
  <div class="info" style="top:305px"><svg width="10" height="10" viewBox="0 0 10 10" fill="#fff"><path d="M5 0l1.5 3.3 3.5.4-2.6 2.4.7 3.5L5 7.8 1.9 9.6l.7-3.5L0 3.7l3.5-.4z"/></svg>Everything is free</div>
  <div class="meters">
    <div><svg width="36" height="36" viewBox="0 0 36 36"><circle cx="18" cy="18" r="15" fill="none" stroke="#ddd" stroke-width="3"/><circle cx="18" cy="18" r="15" fill="none" stroke="var(--gold)" stroke-width="3" stroke-dasharray="70.7 94.2" transform="rotate(-90 18 18)"/><text x="18" y="21" font-size="8" text-anchor="middle" fill="#fff" font-weight="700">75%</text></svg>Percentage</div>
    <div><svg width="36" height="36" viewBox="0 0 36 36"><circle cx="18" cy="18" r="15" fill="none" stroke="var(--pink)" stroke-width="3"/><path d="M18 3a15 15 0 000 30" fill="none" stroke="var(--blue)" stroke-width="3"/></svg>M/F Ratio</div>
  </div>
  <div class="btn pink half-l" style="top:410px"><svg width="22" height="14" viewBox="0 0 22 14" fill="none" stroke="#fff" stroke-width="1.5"><path d="M21 7H2M8 1L2 7l6 6"/></svg></div>
  <div class="btn blue half-r" style="top:410px"><svg width="22" height="14" viewBox="0 0 22 14" fill="none" stroke="#fff" stroke-width="1.5"><path d="M1 7h19M14 1l6 6-6 6"/></svg></div>
</section>

<!-- Create event -->
<section class="screen" style="left:616px;top:518px">
  <div class="backdrop" role="img" aria-label="Blurred concert crowd with stage lights in blue and pink"></div>
  <div class="status"><span>●●●○○ CELL</span><span class="time">4:21 PM</span><span class="batt">100% <i></i></span></div>
  <div class="header">
    <svg class="left" viewBox="0 0 24 24" fill="none" stroke="#fff" stroke-width="2"><path d="M22 12H3M11 4l-8 8 8 8"/></svg>
    <h1>Create Event</h1>
    <svg class="right" viewBox="0 0 24 24" stroke="#fff" stroke-width="2"><path d="M4 4l16 16M20 4L4 20"/></svg>
  </div>
  <div class="form">
    <div class="r"><label>Name:</label><span></span></div>
    <div class="r"><label>Where:</label><span></span></div>
    <div class="r"><label>When:</label><span></span></div>
    <div class="r"><label>Cost:</label><span></span></div>
    <div class="r"><label>Special:</label><span></span></div>
  </div>
  <div class="btn blue wide" style="top:262px"><svg width="20" height="16" viewBox="0 0 20 16" fill="none" stroke="#fff"><rect x=".5" y=".5" width="19" height="15"/><path d="M2 13l5-5 4 4 3-3 4 4"/><circle cx="14" cy="5" r="1.5"/></svg>Upload Event Photo</div>
  <div class="btn blue wide" style="top:308px"><svg width="16" height="16" viewBox="0 0 16 16" fill="none" stroke="#fff"><path d="M1 8l7-7h7v7l-7 7z"/><circle cx="11.5" cy="4.5" r="1"/></svg>Add Ticket</div>
  <div class="terms">Terms of Agreements</div>
  <div class="btn purple wide" style="top:410px">Create Event</div>
</section>

<!-- Tickets -->
<section class="screen" style="left:909px;top:518px">
  <div class="backdrop" role="img" aria-label="Blurred concert crowd with stage lights in blue and pink"></div>
  <div class="status"><span>●●●○○ CELL</span><span class="time">4:21 PM</span><span class="batt">100% <i></i></span></div>
  <div class="header">
    <svg class="left" viewBox="0 0 24 24" stroke="#fff" stroke-width="2"><path d="M1 5h22M1 12h22M1 19h22"/></svg>
    <h1>Tickets</h1>
  </div>
  <div class="form">
    <div class="r"><label>Event:</label><span>Sunwave Festival 2014</span></div>
    <div class="r"><label>Where:</label><span>Coral City, Philippines</span></div>
    <div class="r"><label>When:</label><span>Friday, 10Jan @ 8:0 AM</span></div>
    <div class="r"><label>Pin:</label><span>0123456</span></div>
    <div class="r"><label>Type:</label><span>Free</span></div>
  </div>
  <div class="btn purple wide" style="top:262px">Go To Event</div>
  <div class="btn pink half-l" style="top:410px"><svg width="22" height="14" viewBox="0 0 22 14" fill="none" stroke="#fff" stroke-width="1.5"><path d="M21 7H2M8 1L2 7l6 6"/></svg></div>
  <div class="btn blue half-r" style="top:410px"><svg width="22" height="14" viewBox="0 0 22 14" fill="none" stroke="#fff" stroke-width="1.5"><path d="M1 7h19M14 1l6 6-6 6"/></svg></div>
</section>

</body>
</html>
```